TalkHarbor - Language Coaching Services

Sleek, innovative, trendy design for Language Coaching business.

TalkHarbor is a new UK based company that provides Language Coaching services. We offer highly personalized on-line and face to face language courses. We also impart learning techniques workshops based on the latest neuroscience research for second-language acquisition.

Target Market(s)

See attached info

Industry/Entity Type

Consulting

Contact Information for Business Card

TalkHarbor
DaniaKV@talkharbor.co.uk
TalkHarbor.co.uk
London, UK

Font styles to use
Sans Serif

```html
<!DOCTYPE html>
<html lang="en">
<head>
<meta charset="utf-8">
<title>TalkHarbor Business Cards</title>
<link rel="stylesheet" href="https://fonts.googleapis.com/css2?family=Montserrat:wght@400;700&family=Open+Sans:wght@400;600;700&display=swap">
<style>
  :root {
    --backdrop: #2b2b2d;
    --card: #f7f8f8;
    --brand-blue: #1a8fd0;
    --deep-blue: #1d5f90;
    --ink: #3a3f45;
    --muted: #9a9da1;
  }
  html, body {
    margin: 0;
    width: 1200px;
    height: 892px;
    overflow: hidden;
    background: var(--backdrop);
  }
  .stage {
    position: relative;
    width: 1200px;
    height: 892px;
  }
  .card {
    position: absolute;
    width: 620px;
    height: 354px;
    background: var(--card);
    box-shadow: 0 10px 30px rgba(0,0,0,0.45);
    display: flex;
    flex-direction: column;
    align-items: center;
    justify-content: center;
    box-sizing: border-box;
  }
  .card-front { left: 90px; top: 50px; }
  .card-back { left: 490px; top: 488px; }

  .brand {
    display: flex;
    flex-direction: column;
    align-items: center;
    gap: 16px;
  }
  .brand-dot {
    width: 96px;
    height: 96px;
    border-radius: 50%;
    border: 7px solid var(--brand-blue);
    box-sizing: border-box;
  }
  .brand-name {
    font-family: "Montserrat", sans-serif;
    font-weight: 700;
    font-size: 38px;
    letter-spacing: 1px;
    color: var(--brand-blue);
    text-transform: uppercase;
  }

  .card-back .brand-dot {
    width: 104px;
    height: 104px;
    border-width: 7px;
  }
  .holder {
    margin-top: 14px;
    text-align: center;
  }
  .holder-name {
    font-family: "Montserrat", sans-serif;
    font-weight: 700;
    font-size: 19px;
    color: var(--deep-blue);
    letter-spacing: 0.5px;
    text-transform: uppercase;
  }
  .holder-role {
    font-family: "Open Sans", sans-serif;
    font-size: 13px;
    color: var(--muted);
    letter-spacing: 1px;
    text-transform: uppercase;
    margin-top: 2px;
  }
  .holder-rule {
    width: 64px;
    height: 2px;
    background: var(--brand-blue);
    margin: 8px auto 0;
  }
  .contact {
    margin-top: 38px;
    font-family: "Open Sans", sans-serif;
    font-size: 14px;
    color: var(--ink);
    display: flex;
    gap: 10px;
  }
  .contact-label {
    font-weight: 700;
    color: var(--deep-blue);
  }
</style>
</head>
<body>
<main class="stage">
  <section class="card card-front" aria-label="Business card front">
    <div class="brand">
      <div class="brand-dot"></div>
      <div class="brand-name">TalkHarbor</div>
    </div>
  </section>

  <section class="card card-back" aria-label="Business card back">
    <div class="brand-dot"></div>
    <div class="holder">
      <div class="holder-name">Ellis Marlow</div>
      <div class="holder-role">President</div>
      <div class="holder-rule"></div>
    </div>
    <div class="contact">
      <span><span class="contact-label">P:</span> 020 7946 0318</span>
      <span><span class="contact-label">E:</span> hello@talkharbor.co.uk</span>
      <span><span class="contact-label">W:</span> talkharbor.co.uk</span>
    </div>
  </section>
</main>
</body>
</html>
```